RTavenor Business Cards & Letterhead

I have a logo but need a design for some new business cards. We are a Design-Build Firm that specializes in the design and construction of commercial projects.
the cards need to be professional. no cartoon stuff.
i would like to have the cards in AI format so I can update the card as needed. Logo is provided.
Our Address is: 4187 Marlowe Ct. Linden Falls, Oregon 27614

```html
<!DOCTYPE html>
<html lang="en">
<head>
<meta charset="utf-8">
<title>RTavenor Business Card</title>
<link href="https://fonts.googleapis.com/css2?family=Montserrat:wght@400;500;700;800&display=swap" rel="stylesheet">
<style>
  :root {
    --backdrop: #3a3a3c;
    --card-light: #ffffff;
    --card-dark: #222222;
    --ink: #1f1f1f;
    --brand-blue: #1a78c2;
    --white: #ffffff;
  }
  * { margin: 0; padding: 0; box-sizing: border-box; }
  html, body { width: 1200px; height: 1059px; overflow: hidden; }
  body {
    background: var(--backdrop);
    font-family: "Montserrat", sans-serif;
    position: relative;
  }
  .card {
    position: absolute;
    border-radius: 20px;
    overflow: hidden;
  }
  .card-front {
    left: 256px; top: 100px; width: 688px; height: 391px;
    background: var(--card-light);
    color: var(--ink);
  }
  .card-back {
    left: 253px; top: 537px; width: 694px; height: 394px;
    background: var(--card-dark);
  }
  .brand {
    position: absolute;
    display: flex; align-items: center; gap: 12px;
    font-weight: 800;
    letter-spacing: -2px;
    line-height: 1;
    white-space: nowrap;
  }
  .brand-mark { background: var(--brand-blue); display: block; flex: none; }
  .card-front .brand { left: 30px; top: 77px; font-size: 68px; color: var(--ink); }
  .card-front .brand-mark { width: 49px; height: 49px; }
  .card-back .brand { left: 50%; top: 165px; transform: translateX(-50%); font-size: 74px; color: var(--white); }
  .card-back .brand-mark { width: 56px; height: 56px; }
  .name-bar {
    position: absolute; left: 0; top: 213px; width: 17px; height: 42px;
    background: var(--brand-blue);
  }
  .person { position: absolute; left: 30px; top: 208px; }
  .person-name { font-weight: 700; font-size: 29px; color: var(--brand-blue); letter-spacing: 0.5px; line-height: 1.1; white-space: nowrap; }
  .person-title { font-size: 19px; font-weight: 400; letter-spacing: 0.5px; line-height: 1.2; }
  .contacts { position: absolute; left: 30px; top: 290px; list-style: none; }
  .contacts li {
    display: flex; align-items: center; gap: 8px;
    font-size: 18px; height: 26.5px; letter-spacing: 0.3px; white-space: nowrap;
  }
  .contacts svg { width: 13px; height: 13px; fill: var(--brand-blue); flex: none; }
  .divider { position: absolute; left: 311px; top: 328px; width: 1px; height: 35px; background: var(--ink); }
  .address { position: absolute; left: 329px; top: 321px; font-size: 18px; line-height: 23px; letter-spacing: 0.3px; font-style: normal; white-space: nowrap; }
</style>
</head>
<body>
  <section class="card card-front">
    <div class="brand"><span class="brand-mark"></span>RTAVENOR</div>
    <div class="name-bar"></div>
    <div class="person">
      <div class="person-name">DANA WHITFIELD</div>
      <div class="person-title">MANAGER</div>
    </div>
    <ul class="contacts">
      <li><svg viewBox="0 0 24 24"><path d="M6.6 10.8a15 15 0 0 0 6.6 6.6l2.2-2.2a1 1 0 0 1 1-.25 11.4 11.4 0 0 0 3.6.6 1 1 0 0 1 1 1V20a1 1 0 0 1-1 1A17 17 0 0 1 3 4a1 1 0 0 1 1-1h3.5a1 1 0 0 1 1 1c0 1.250.2 2.450.6 3.6a1 1 0 0 1-.25 1z"/></svg>123-456-7890</li>
      <li><svg viewBox="0 0 24 24"><path d="M2 5h20v2l-10 6L2 7z M2 9l10 6 10-6v10H2z"/></svg>info@youremail.com</li>
      <li><svg viewBox="0 0 24 24"><path d="M12 2a10 10 0 1 0 0 20 10 10 0 0 0 0-20zm0 2c.9 1.2 1.6 2.6 2 4h-4c.4-1.4 1.1-2.8 2-4zM4.3 14a8 8 0 0 1 0-4h3.4a16 16 0 0 0 0 4zm.8 2h3c.3 1.3.8 2.5 1.4 3.6A8 8 0 0 1 5.1 16zM8 8H5.1a8 8 0 0 1 4.4-3.6C8.8 5.5 8.4 6.7 8 8zm4 12c-.9-1.2-1.6-2.6-2-4h4c-.4 1.4-1.1 2.8-2 4zm2.3-6H9.7a14 14 0 0 1 0-4h4.6a14 14 0 0 1 0 4zm.2 5.6c.6-1.1 1.1-2.3 1.4-3.6h3a8 8 0 0 1-4.4 3.6zm1.8-5.6a16 16 0 0 0 0-4h3.4a8 8 0 0 1 0 4zM16 8c-.3-1.3-.8-2.5-1.5-3.6A8 8 0 0 1 18.9 8z"/></svg>www.yourwebsite.com</li>
    </ul>
    <div class="divider"></div>
    <address class="address">4187 Marlowe Ct.<br>Linden Falls, Oregon 27614</address>
  </section>
  <section class="card card-back">
    <div class="brand"><span class="brand-mark"></span>RTAVENOR</div>
  </section>
</body>
</html>
```